Construction company business card

One side to be the logo with the company name, The other side I would like: (Tomas verbick) Project manager 41 barrow crescent linford 52917306224783(03) 9703 2428Info@gudeljgroup.comAnd then maybe a couple dot points saying what we do:Construction (commercial & industrial) Civil construction

Anything else please contact me!
Maybe curved st one edge of the card

Target Market(s)

Older clientele

Industry/Entity Type

Construction Company

Contact Information for Business Card

Read above

Colors
3277b5
1b1b1b
9d9d9d

Requirements
Must have
• Use my logo on one side
Nice to have
• Read above
Should not have
• Read above

```html
<!DOCTYPE html>
<html lang="en">
<head>
<meta charset="utf-8">
<title>Ironvale Construction – Business Card</title>
<link href="https://fonts.googleapis.com/css2?family=Work+Sans:wght@400;500;600&display=swap" rel="stylesheet">
<style>
  :root {
    --stage: #161616;
    --card: #1b1b1b;
    --card-edge: #262626;
    --brand-blue: #3277b5;
    --silver: #9d9d9d;
    --ink-light: #f2f2f2;
  }
  * { box-sizing: border-box; margin: 0; padding: 0; }
  html, body {
    width: 1200px;
    height: 900px;
    overflow: hidden;
    background: var(--stage);
    font-family: "Work Sans", Arial, sans-serif;
  }
  .canvas {
    width: 1200px;
    height: 900px;
    display: flex;
    flex-direction: column;
    align-items: center;
    justify-content: center;
    gap: 40px;
  }
  .card {
    position: relative;
    width: 680px;
    height: 389px;
    background: var(--card);
    border: 1px solid var(--card-edge);
  }

  /* Front side */
  .card-front {
    display: flex;
    align-items: center;
    justify-content: center;
  }
  .brand {
    display: flex;
    align-items: center;
    gap: 16px;
  }
  .brand-dot {
    width: 34px;
    height: 34px;
    border-radius: 50%;
    background: var(--silver);
  }
  .brand-name {
    font-size: 30px;
    font-weight: 600;
    letter-spacing: 0.06em;
    text-transform: uppercase;
    color: var(--silver);
  }

  /* Back side */
  .identity {
    position: absolute;
    left: 60px;
    top: 148px;
    width: 225px;
    text-align: right;
  }
  .person-name {
    font-size: 27px;
    font-weight: 500;
    letter-spacing: 0.03em;
    text-transform: uppercase;
    color: var(--brand-blue);
    white-space: nowrap;
  }
  .person-role {
    margin-top: 2px;
    font-size: 20px;
    font-weight: 400;
    letter-spacing: 0.04em;
    color: var(--ink-light);
  }
  .divider {
    position: absolute;
    left: 302px;
    top: 150px;
    width: 2px;
    height: 68px;
    background: var(--brand-blue);
  }
  .contact-list {
    position: absolute;
    left: 322px;
    top: 152px;
    list-style: none;
  }
  .contact-item {
    display: flex;
    align-items: center;
    gap: 10px;
    height: 24px;
    font-size: 18px;
    letter-spacing: 0.06em;
    color: var(--ink-light);
  }
  .contact-icon {
    width: 13px;
    height: 13px;
    flex: none;
  }
  .address {
    position: absolute;
    left: 0;
    right: 0;
    top: 318px;
    text-align: center;
    font-size: 19px;
    letter-spacing: 0.06em;
    color: var(--ink-light);
  }
</style>
</head>
<body>
<main class="canvas">

  <section class="card card-front" aria-label="Card front">
    <div class="brand">
      <span class="brand-dot"></span>
      <span class="brand-name">Ironvale Construction</span>
    </div>
  </section>

  <section class="card card-back" aria-label="Card back">
    <div class="identity">
      <p class="person-name">Tomas Verbick</p>
      <p class="person-role">Project manager</p>
    </div>
    <span class="divider"></span>
    <ul class="contact-list">
      <li class="contact-item">
        <svg class="contact-icon" viewBox="0 0 16 16" fill="none" stroke="#3277b5" stroke-width="1.6" stroke-linecap="round" stroke-linejoin="round">
          <path d="M4 1.5 6 5 4.5 6.5c1 2 3 4 5 5L11 10l3.5 2-1 2.5C8 14.5 1.5 8 1.5 2.5z"/>
        </svg>
        73 0622 4783
      </li>
      <li class="contact-item">
        <svg class="contact-icon" viewBox="0 0 16 16" fill="none" stroke="#3277b5" stroke-width="1.6">
          <rect x="4" y="1.5" width="8" height="13" rx="1.5"/>
          <line x1="7" y1="12" x2="9" y2="12"/>
        </svg>
        03 9418 6573
      </li>
      <li class="contact-item">
        <svg class="contact-icon" viewBox="0 0 16 16" fill="none" stroke="#3277b5" stroke-width="1.4" stroke-linejoin="round">
          <rect x="1.5" y="3.5" width="13" height="9"/>
          <path d="M1.5 3.5 8 9l6.5-5.5"/>
        </svg>
        Info@verbickgroup.com
      </li>
    </ul>
    <p class="address">41 barrow crescent linford 5291</p>
  </section>

</main>
</body>
</html>
```